Business Intelligence Application - Reporting Menu and Report Criteria Design

Looking for a fresh, effective and user friendly view for the menu structure and reporting criteria screen format for a business reporting application. Initial format completed, content structure is in place, but we need the 'wow' design.. as its a serious professional report/BI tool it has to fall within certain guidelines for clarity and graphics..but we want it to be slick, friendly, great user experience. There is a large amount of complex content to fit into a small space and we need it to be very inviting, modern and intuitive.. If interested, please review the attachment. We have live screens in operation, but feel these could be improved and looking forward to seeing what great creative suggestions could be made. Please review work done to date in the attached.. We are not looking for a total re-design of everything, all the basic business content/structure is there.. but tell us what we could do to improve this in terms of graphic design... particularly the criteria screens.. thanks!
Updates

Reason: Need a few more days to review designs - thanks for all submissions so far, we will make a selection shortly.

Target Market(s)

Business analysts, hotel operations teams, finance analysts hospitality industry

Industry/Entity Type

Hospitality

Coding

Coded - Design and coding required

Number of Pages Required

4 page

Font styles to use
Sans Serif
Other font styles liked:
• Candara, please see example in deck

Colors
3276b5
3176b5
0255a3
85acd3
33a6d7
cee9f5
85cae6

Requirements
Must have
• sharp clear, logical menu structure, (currently it has 'clicks to sub-menus, we need hover over, slide to sub-menus..) colour, styling.. and most focus on revision of criteria.. right now is somewhat heavy, cumbersome.. keep colour and friendly intuitive process steps.. its heavy analytical stuff.. best of luck!
Should not have
• No grey fonts on white or grey screens! many business apps are not readable or sharp.. or fonts are too small.. colourless, so please avoid that.. see our deck - sharp dark (navy) or black fonts on white, or light shading..

```html
<!DOCTYPE html>
<html lang="en">
<head>
<meta charset="utf-8">
<title>RevSight – Admin Setup</title>
<link rel="stylesheet" href="https://fonts.googleapis.com/css2?family=Lato:ital,wght@0,400;0,700;0,900;1,400&family=Open+Sans:wght@400;600&display=swap">
<style>
:root{
  --navy-deep:#04193a;
  --sidebar:#0255a3;
  --sidebar-active:#0a4788;
  --sidebar-line:#2a6cb0;
  --accent:#33a6d7;
  --avatar:#85acd3;
  --page:#d2d2d2;
  --panel:#d9d9d9;
  --panel-head:#c8c8c8;
  --tab:#cdcdcd;
  --tab-line:#a9a9a9;
  --ink:#1d1d1d;
  --ink-soft:#3a3a3a;
  --white:#ffffff;
  --menu-hover:#e6e6e6;
  --rule:#9c9c9c;
}
*{box-sizing:border-box;margin:0;padding:0}
html,body{width:1200px;height:736px;overflow:hidden}
body{position:relative;background:var(--page);font-family:"Open Sans",sans-serif;color:var(--ink)}
.abs{position:absolute}

/* brand & header */
.brand{left:0;top:0;width:252px;height:82px;background:var(--navy-deep);display:flex;align-items:center;justify-content:center;gap:10px}
.brand-dot{width:16px;height:16px;border-radius:50%;background:var(--accent)}
.brand-name{font-family:"Lato",sans-serif;font-weight:700;font-size:24px;color:var(--white)}
.topbar{left:252px;top:0;width:948px;height:82px;background:var(--white);box-shadow:0 2px 3px rgba(0,0,0,.12)}
.avatar{left:784px;top:14px;width:55px;height:55px;border-radius:50%;background:var(--avatar);border:3px solid #e4e4e4;overflow:hidden}
.welcome{left:856px;top:19px;font-family:"Lato",sans-serif;font-weight:700;font-size:16px;color:#333}
.today{left:856px;top:47px;font-family:"Lato",sans-serif;font-style:italic;font-size:12px;color:#555;display:flex;align-items:center;gap:6px}
.round-btn{top:21px;width:41px;height:41px;border-radius:50%;border:1px solid #777;background:var(--white);display:flex;align-items:center;justify-content:center}
.btn-alerts{left:1052px}
.btn-logout{left:1110px}

/* sidebar */
.sidebar{left:0;top:82px;width:252px;height:654px;background:var(--sidebar)}
.nav-item{position:absolute;left:0;width:252px;height:62px;display:flex;align-items:center;font-family:"Lato",sans-serif;font-weight:700;font-size:16px;color:var(--white);letter-spacing:.2px}
.nav-item svg{position:absolute;left:32px}
.nav-item span{position:absolute;left:76px}
.nav-item.active{background:var(--sidebar-active)}
.nav-item.ruled{border-bottom:1px solid var(--sidebar-line)}

/* search */
.search{left:292px;top:114px;width:857px;height:48px;background:#c7c7c7;border:1px solid #aaa}
.search-tool{left:1090px;top:114px;width:59px;height:48px;border:1px solid #aaa;background:#cbcbcb;display:flex;align-items:center;justify-content:center}
.search-tool i{width:32px;height:32px;border-radius:50%;background:#8a6a4a;display:block}

/* tabs */
.tab{top:199px;height:50px;width:134px;background:var(--tab);border:1px solid var(--tab-line);display:flex;align-items:center;justify-content:center;text-align:center;font-family:"Lato",sans-serif;font-weight:700;font-size:15px;line-height:1.05;color:var(--ink)}
.tab.active{background:#2f8fc2;color:var(--white);border-color:#2f8fc2}

/* select panel */
.select-panel{left:291px;top:309px;width:467px;height:309px;background:var(--panel);border-top:3px solid var(--accent);box-shadow:0 1px 3px rgba(0,0,0,.25)}
.select-head{position:absolute;left:0;top:0;width:100%;height:47px;background:var(--panel-head);font-family:"Lato",sans-serif;font-weight:900;font-size:22px;padding:10px 0 0 27px;color:#1a1a1a}
.scroll-track{position:absolute;right:0;top:47px;width:19px;bottom:0;background:#dedede;border-left:1px solid #cfcfcf}
.prop-row{position:absolute;left:25px;width:392px;height:43px;border-bottom:1px solid #a7a7a7;display:flex;justify-content:space-between;align-items:center;font-size:14px;color:var(--ink-soft)}
.footer-rule{left:292px;top:655px;width:809px;height:1px;background:var(--rule)}
.copyright{left:292px;top:688px;width:809px;text-align:center;font-size:12px;color:#333}
.build-tag{left:1159px;top:705px;font-family:"Lato",sans-serif;font-weight:700;font-size:14px;color:#333}

/* menus */
.menu{background:var(--white);box-shadow:0 1px 4px rgba(0,0,0,.3)}
.admin-menu{left:252px;top:118px;width:147px;height:193px}
.setup-menu{left:399px;top:213px;width:191px;height:339px}
.menu-item{position:absolute;left:0;width:100%;height:36px;display:flex;align-items:center;font-size:14px;color:#2b2b2b}
.admin-menu .menu-item{padding-left:31px}
.setup-menu .menu-item{padding-left:24px}
.menu-item.hover{background:var(--menu-hover)}
</style>
</head>
<body>

<header>
  <div class="abs brand"><i class="brand-dot"></i><span class="brand-name">RevSight</span></div>
  <div class="abs topbar"></div>
  <div class="abs avatar">
    <svg width="49" height="49" viewBox="0 0 49 49"><circle cx="24.5" cy="19" r="8" fill="#fff"/><path d="M10 38c0-8 6-11 14.5-11S39 30 39 38v4H10z" fill="#fff"/></svg>
  </div>
  <div class="abs welcome">Welcome Admin</div>
  <div class="abs today">
    <svg width="11" height="11" viewBox="0 0 11 11"><rect x="0.5" y="1.5" width="10" height="9" fill="none" stroke="#777"/><rect x="0.5" y="1.5" width="10" height="2.5" fill="#777"/></svg>
    Tuesday October 03, 2017
  </div>
  <div class="abs round-btn btn-alerts">
    <svg width="16" height="16" viewBox="0 0 16 16"><path d="M8 1c3 0 4.5 2.3 4.5 5v3.5L14 12H2l1.5-2.5V6C3.5 3.3 5 1 8 1z" fill="#33a6d7"/><circle cx="8" cy="14" r="1.6" fill="#33a6d7"/></svg>
  </div>
  <div class="abs round-btn btn-logout">
    <svg width="16" height="16" viewBox="0 0 16 16"><path d="M2 3h5v2H4v6h3v2H2z" fill="#33a6d7"/><path d="M8 5.5h3V3l4 5-4 5v-2.5H8z" fill="#33a6d7"/></svg>
  </div>
</header>

<nav class="abs sidebar">
  <div class="nav-item active" style="top:38px">
    <svg width="22" height="22" viewBox="0 0 22 22"><circle cx="11" cy="6" r="5" fill="#fff"/><path d="M2 21c0-6 4-8 9-8s9 2 9 8z" fill="#fff"/></svg>
    <span>ADMIN</span></div>
  <div class="nav-item ruled" style="top:108px;height:62px">
    <svg width="26" height="22" viewBox="0 0 26 22"><circle cx="13" cy="6" r="4" fill="#fff"/><circle cx="5" cy="8" r="3" fill="#fff"/><circle cx="21" cy="8" r="3" fill="#fff"/><path d="M6 21c0-6 3-8 7-8s7 2 7 8z" fill="#fff"/><path d="M0 19c0-4 2-6 5-6s4 1 4 2v4z" fill="#fff"/><path d="M26 19c0-4-2-6-5-6s-4 1-4 2v4z" fill="#fff"/></svg>
    <span>MANAGEMENT</span></div>
  <div class="nav-item ruled" style="top:178px;height:62px">
    <svg width="22" height="22" viewBox="0 0 22 22"><circle cx="9" cy="9" r="6.5" fill="none" stroke="#fff" stroke-width="3"/><path d="M14 14l6 6" stroke="#fff" stroke-width="3.5" stroke-linecap="round"/></svg>
    <span>PROPERTY SEARCH</span></div>
  <div class="nav-item ruled" style="top:248px;height:62px">
    <svg width="26" height="22" viewBox="0 0 26 22"><circle cx="8" cy="12" r="6" fill="none" stroke="#fff" stroke-width="3.5" stroke-dasharray="3 2"/><circle cx="8" cy="12" r="2" fill="#fff"/><circle cx="20" cy="6" r="4" fill="none" stroke="#fff" stroke-width="2.5" stroke-dasharray="2 1.5"/><circle cx="20" cy="17" r="3.5" fill="none" stroke="#fff" stroke-width="2.5" stroke-dasharray="2 1.5"/></svg>
    <span>INTEL</span></div>
  <div class="nav-item" style="top:320px">
    <svg width="22" height="22" viewBox="0 0 22 22"><circle cx="11" cy="8" r="5.5" fill="none" stroke="#fff" stroke-width="2"/><rect x="8.5" y="14" width="5" height="5" rx="1" fill="none" stroke="#fff" stroke-width="2"/></svg>
    <span>PLANNING</span></div>
</nav>

<main>
  <div class="abs search"></div>
  <div class="abs search-tool"><i role="img" aria-label="Connected service badge"></i></div>

  <div class="abs tab active" style="left:292px">PROPERTIES</div>
  <div class="abs tab" style="left:437px">BRANDS</div>
  <div class="abs tab" style="left:581px">SEARCH<br>PRODUCT</div>
  <div class="abs tab" style="left:726px">DIVISIONS</div>
  <div class="abs tab" style="left:870px">REGIONS</div>
  <div class="abs tab" style="left:1015px">AREAS</div>

  <section class="abs select-panel">
    <div class="select-head">SELECT PROPERTY</div>
    <div class="scroll-track">
      <svg width="19" height="306" viewBox="0 0 19 306"><path d="M6 17l3.5-4 3.5 4z" fill="#aaa"/><path d="M6 287l3.5 4 3.5-4z" fill="#aaa"/></svg>
    </div>
    <div class="prop-row" style="top:74px"><span>Harbor Point</span><span>RHDOH</span></div>
    <div class="prop-row" style="top:115px"><span>Palm Cove</span><span>123</span></div>
    <div class="prop-row" style="top:158px"><span>Harbor Point</span><span>RHDOH</span></div>
    <div class="prop-row" style="top:204px"><span>Palm Cove</span><span>123</span></div>
  </section>

  <div class="abs footer-rule"></div>
  <div class="abs copyright">Copyright © 2017, RevSight. All rights reserved.</div>
  <div class="abs build-tag">C17</div>
</main>

<div class="abs menu admin-menu">
  <div class="menu-item" style="top:22px">Registration</div>
  <div class="menu-item" style="top:59px">User Access</div>
  <div class="menu-item hover" style="top:96px">Setup</div>
  <div class="menu-item" style="top:132px">Data Imports</div>
</div>

<div class="abs menu setup-menu">
  <div class="menu-item" style="top:19px">Market Segments</div>
  <div class="menu-item" style="top:56px">Banquet &amp; Catering</div>
  <div class="menu-item" style="top:93px">Outlets/F&amp;B Service</div>
  <div class="menu-item" style="top:130px">Other Income</div>
  <div class="menu-item" style="top:167px">Impact Dates</div>
  <div class="menu-item" style="top:204px">Inventory</div>
  <div class="menu-item" style="top:240px">Geo/Location</div>
  <div class="menu-item" style="top:277px">Distribution Channels</div>
</div>

</body>
</html>
```